New, modern business card for growing audiology practice

We need a new business card for our audiology practice. Our logo and website have recently changed (more modern) and we want our business cards to reflect this change.
We conduct hearing tests, perform earwax removals, and fit & dispense hearing aids to our patients. We are a family owned practice in which the owner is the one who works directly with the patient. I have attached logos in various formats to use, as well as two ideas I found on this website; as well as a scanned copy of our current logo. Good luck!

Industry/Entity Type

Business

Contact Information for Business Card

Company name: Tolvera Hearing Center
Provider name: Peter Wolstenby, Au.D. F/NSB
Phone number: (555) 683-5127
Address: 837 W. Lindell Ave. Marlow Brook, OH 40917
email: tolverahearing@postvane.com
website: tolverahearing.com

Colors
000000
aaaaaa
dbdbdb
cacaca
9bcb3c
afd23c
cadf82
b1b1b1

Requirements
Must have
• My card must include information in the "details" section. In the attached images, I found a few that I liked and I would like to model after - "brisky bouncin'" and "Sound Method Center".
• Must be horizontal.
• Must include logos provided. I uploaded them in various file formats and various ways.
• Must match logo font, if possible, if not, please get as close as you can.
Nice to have
• I really like the idea of having a color on one side with just the logo and company name and the contact information and provider name on the other side. I also really like the idea of having the main color dominating on the logo/company side with accent of that same color on the contact side of the card.
Should not have
• Must not be vertical.

```html
<!DOCTYPE html>
<html lang="en">
<head>
<meta charset="utf-8">
<title>Tolvera Hearing Center — Business Card</title>
<link rel="stylesheet" href="https://fonts.googleapis.com/css2?family=Lato:wght@400;700&family=Roboto:wght@400;500&family=Roboto+Condensed:wght@500;700&display=swap">
<style>
  :root {
    --backdrop: #e4e1dc;
    --card-white: #f2f2f2;
    --brand-green: #71a036;
    --ink-black: #000000;
    --ink-dark: #1a1a1a;
    --text-white: #ffffff;
  }
  * { margin: 0; padding: 0; box-sizing: border-box; }
  html, body {
    width: 1200px;
    height: 960px;
    overflow: hidden;
    background: var(--backdrop);
  }
  .canvas {
    position: relative;
    width: 1200px;
    height: 960px;
  }
  .card {
    position: absolute;
    width: 600px;
    height: 343px;
    overflow: hidden;
    box-shadow: 0 2px 6px rgba(0, 0, 0, 0.35);
  }
  .card-front {
    left: 314px;
    top: 113px;
    background: var(--card-white);
  }
  .card-back {
    left: 311px;
    top: 472px;
    background: var(--ink-black);
  }
  .front-swoosh {
    position: absolute;
    inset: 0;
    width: 600px;
    height: 343px;
  }
  .brand-name {
    position: absolute;
    font-family: "Lato", sans-serif;
    font-weight: 400;
    text-transform: uppercase;
    white-space: nowrap;
  }
  .card-front .brand-name {
    left: 67px;
    top: 85px;
    font-size: 18.5px;
    color: var(--ink-dark);
  }
  .provider {
    position: absolute;
    right: 22px;
    top: 187px;
    text-align: right;
    color: var(--text-white);
  }
  .provider-name {
    font-family: "Roboto Condensed", sans-serif;
    font-weight: 500;
    font-size: 21px;
    line-height: 26px;
  }
  .provider-credentials {
    font-family: "Roboto", sans-serif;
    font-weight: 500;
    font-size: 15px;
    line-height: 22px;
    letter-spacing: 0.6px;
  }
  .contact-list {
    position: absolute;
    right: 22px;
    top: 244px;
    list-style: none;
    text-align: right;
    font-family: "Roboto", sans-serif;
    font-size: 14.5px;
    line-height: 19px;
    color: var(--text-white);
  }
  .contact-list li {
    display: flex;
    justify-content: flex-end;
    align-items: center;
    gap: 5px;
  }
  .contact-icon {
    width: 13px;
    height: 13px;
    fill: var(--text-white);
  }
  .address {
    position: absolute;
    right: 20px;
    top: 307px;
    font-family: "Roboto", sans-serif;
    font-size: 14.5px;
    color: var(--text-white);
    white-space: nowrap;
  }
  .card-back .brand-name {
    left: 0;
    right: 0;
    top: 153px;
    text-align: center;
    font-size: 30px;
    color: var(--text-white);
  }
  .back-website {
    position: absolute;
    left: 0;
    right: 0;
    top: 286px;
    text-align: center;
    font-family: "Roboto", sans-serif;
    font-size: 14px;
    letter-spacing: 5px;
    color: var(--text-white);
  }
</style>
</head>
<body>
<main class="canvas">

  <section class="card card-front" aria-label="Card front">
    <svg class="front-swoosh" viewBox="0 0 600 343" aria-hidden="true">
      <path fill="var(--ink-black)" d="M0,248 C30,288 70,299 112,298 C262,294 452,150 600,37 L600,343 L0,343 Z"/>
      <path fill="var(--brand-green)" d="M0,256 C40,298 85,305 125,304 C275,298 462,154 600,41 L600,343 L0,343 Z"/>
      <path fill="none" stroke="var(--card-white)" stroke-width="2" d="M0,256 C40,298 85,305 125,304 C275,298 462,154 600,41"/>
    </svg>

    <p class="brand-name">Tolvera Hearing Center</p>

    <div class="provider">
      <p class="provider-name">PETER WOLSTENBY</p>
      <p class="provider-credentials">AU.D. F/NSB</p>
    </div>

    <ul class="contact-list">
      <li>(555) 683-5127
        <svg class="contact-icon" viewBox="0 0 24 24" aria-hidden="true"><path d="M6.6 10.8a15.2 15.2 0 0 0 6.6 6.6l2.2-2.2a1 1 0 0 1 1-.25 11.4 11.4 0 0 0 3.6.57 1 1 0 0 1 1 1V20a1 1 0 0 1-1 1A17 17 0 0 1 3 4a1 1 0 0 1 1-1h3.5a1 1 0 0 1 1 1c0 1.25.2 2.45.57 3.57a1 1 0 0 1-.25 1z"/></svg>
      </li>
      <li>tolverahearing@postvane.com
        <svg class="contact-icon" viewBox="0 0 24 24" aria-hidden="true"><path d="M2 5h20v2l-10 6L2 7zM2 9l10 6 10-6v10H2z"/></svg>
      </li>
      <li>tolverahearing.com
        <svg class="contact-icon" viewBox="0 0 24 24" aria-hidden="true"><circle cx="12" cy="12" r="11"/><path fill="none" stroke="var(--brand-green)" stroke-width="1.6" d="M1 12h22M12 1c-4 3-4 19 0 22M12 1c4 3 4 19 0 22"/></svg>
      </li>
    </ul>

    <p class="address">837 W. Lindell Ave., Marlow Brook, OH 40917</p>
  </section>

  <section class="card card-back" aria-label="Card back">
    <p class="brand-name">Tolvera Hearing Center</p>
    <p class="back-website">www.tolverahearing.com</p>
  </section>

</main>
</body>
</html>
```